Website for new dental office

I am Dr. Colin Ashford and am building a new dental practice. I specialize in general dentistry. I am young and have a higher end dental practice incorporating very new technologies and would like my website to reflect that. As many dental patients are older, the website must be very easy to navigate. I would like patients to be able to request appointments, and will eventually add on patient information forms (the health history, etc, that you normally fill out in the practice) from my practice management software, so leave an area for that.

Industry/Entity Type

Building

```html
<!DOCTYPE html>
<html lang="en">
<head>
<meta charset="utf-8">
<title>Colin Ashford, DDS – Our Team</title>
<link href="https://fonts.googleapis.com/css2?family=Open+Sans:wght@300;400;600;700&display=swap" rel="stylesheet">
<style>
:root{
  --blue:#1e8ee0;
  --blue-dark:#135a9c;
  --blue-deep:#0f4f8c;
  --nav-top:#3a95e4;
  --nav-bottom:#1d6fc4;
  --logo:#2467ae;
  --text:#333;
  --muted:#666;
  --orange-top:#fbab3c;
  --orange-bottom:#f27b12;
  --panel:#f6f6f6;
  --line:#e2e2e2;
}
*{box-sizing:border-box;margin:0;padding:0}
html,body{width:1200px;height:1095px;overflow:hidden;background:#fff}
body{font-family:"Open Sans",Arial,sans-serif;color:var(--text);position:relative}
.site-header{position:absolute;top:0;left:0;width:1200px;height:117px;background:linear-gradient(#cfe6fb,#fff 80%)}
.brand{position:absolute;left:115px;top:38px;font-size:36px;font-weight:600;color:var(--logo);letter-spacing:.5px}
.hotline{position:absolute;left:830px;top:36px;display:flex;align-items:center;gap:10px;font-size:28px;color:#444}
.main-nav{position:absolute;top:117px;left:0;width:1200px;height:44px;background:linear-gradient(var(--nav-top),var(--nav-bottom))}
.main-nav a{position:absolute;top:0;height:44px;line-height:44px;color:#fff;text-decoration:none;font-size:15px;text-align:center}
.main-nav a.home{font-weight:700}
.main-nav a.active{background:var(--blue-deep)}
.main-nav .sep{position:absolute;top:10px;width:1px;height:26px;background:rgba(255,255,255,.25)}
.hero{position:absolute;top:161px;left:0;width:1200px;height:253px;background:linear-gradient(90deg,#dfe6ec,#f3f6f9 45%,#e6eaee)}
.hero-photo{position:absolute;right:0;top:0;width:480px;height:253px;background:linear-gradient(90deg,rgba(230,235,240,0),#cfdbe5 40%,#e8eef3)}
.hero h1{position:absolute;left:110px;top:58px;font-size:58px;font-weight:300;color:var(--blue-dark);line-height:1}
.hero h1 b{font-weight:700}
.hero p{position:absolute;left:110px;top:132px;width:480px;font-size:20px;line-height:27px;color:#333}
.section-title{position:absolute;top:463px;left:108px;font-size:24px;color:var(--blue)}
.title-rule{position:absolute;top:479px;left:238px;width:848px;height:4px;border-bottom:1px dotted #bbb}
.title-rule::before{content:"";position:absolute;left:0;top:0;width:116px;height:4px;background:var(--blue)}
.member{position:absolute;top:536px;width:200px;text-align:center}
.member .photo{display:block;margin:0 auto;width:163px;height:163px;border:1px solid #ccc;background:linear-gradient(#e9edf0,#c9d2da)}
.member h3{margin-top:10px;font-size:22px;font-weight:400;color:#333}
.member .role{font-size:15px;color:var(--blue);margin-top:1px}
.member p{font-size:12px;line-height:16px;color:var(--muted);margin-top:8px}
.cta{position:absolute;top:900px;left:107px;width:983px;height:104px;background:var(--panel);border:1px solid var(--line);border-radius:8px}
.cta h2{position:absolute;left:16px;top:33px;font-size:26px;font-weight:400;color:#555}
.cta .btn{position:absolute;left:756px;top:23px;width:208px;height:58px;border-radius:3px;background:linear-gradient(var(--orange-top),var(--orange-bottom));color:#fff;font-size:19px;display:flex;align-items:center;padding-left:8px;gap:12px;text-decoration:none}
.site-footer{position:absolute;top:1041px;left:0;width:1200px;text-align:center;font-size:13px;color:#222}
</style>
</head>
<body>
<header class="site-header">
  <div class="brand">Colin Ashford, DDS</div>
  <div class="hotline">
    <svg width="42" height="42" viewBox="0 0 42 42" aria-hidden="true">
      <circle cx="24" cy="18" r="14" fill="none" stroke="#1e8ee0" stroke-width="2.5"/>
      <text x="24" y="23" font-family="Open Sans,sans-serif" font-size="13" font-weight="700" fill="#1e8ee0" text-anchor="middle">24</text>
      <path d="M5 8c-4 6 2 20 14 28l6-3-5-6-4 2c-3-3-6-8-7-12l4-2-3-7z" fill="#333"/>
    </svg>
    <span>+123 555 0147</span>
  </div>
</header>
<nav class="main-nav">
  <a class="home" style="left:96px;width:76px">HOME</a>
  <a style="left:210px;width:100px">ABOUT US</a><span class="sep" style="left:324px"></span>
  <a style="left:345px;width:92px">SERVICES</a><span class="sep" style="left:456px"></span>
  <a style="left:475px;width:105px">RESOURCES</a><span class="sep" style="left:600px"></span>
  <a style="left:620px;width:85px">GALLERY</a><span class="sep" style="left:725px"></span>
  <a style="left:745px;width:68px">CASES</a>
  <a class="active" style="left:831px;width:107px">TEAM</a>
  <a style="left:952px;width:90px">CONTACT</a>
</nav>
<section class="hero">
  <h1>Our <b>Team</b></h1>
  <p>Lorem Ipsum is simply dummy text of the printing and typesetting industry. Lorem Ipsum has been</p>
  <div class="hero-photo" role="img" aria-label="Photo of a smiling dentist and a nurse holding a clipboard in a bright clinic"></div>
</section>
<h2 class="section-title">Our Team</h2>
<div class="title-rule"></div>
<article class="member" style="left:98px">
  <div class="photo" role="img" aria-label="Portrait of the dentist"></div>
  <h3>Dr Ashford</h3><div class="role">Doctor</div>
  <p>Lorem Ipsum is simply dummy<br>text of the printing and typeset-<br>ting industry. Lorem Ipsum has<br>been the industry's standard<br>dummy text ever since.</p>
</article>
<article class="member" style="left:377px">
  <div class="photo" role="img" aria-label="Portrait of the administrator"></div>
  <h3 style="margin-top:8px">Miss Brooke</h3><div class="role">Administrator</div>
  <p>Lorem Ipsum is simply dummy<br>text of the printing and typeset-<br>ting industry. Lorem Ipsum has<br>been the industry's standard<br>dummy text ever since.</p>
</article>
<article class="member" style="left:631px">
  <div class="photo" role="img" aria-label="Portrait of the dental assistant"></div>
  <h3>Mr Aldrich</h3><div class="role">Dental Assistant</div>
  <p>Lorem Ipsum is simply dummy<br>text of the printing and typeset-<br>ting industry. Lorem Ipsum has<br>been the industry's standard<br>dummy text ever since.</p>
</article>
<article class="member" style="left:896px">
  <div class="photo" role="img" aria-label="Portrait of the hygienist"></div>
  <h3>Miss Samantha</h3><div class="role">Hygienist at First</div>
  <p>Lorem Ipsum is simply dummy<br>text of the printing and typeset-<br>ting industry. Lorem Ipsum has<br>been the industry's standard<br>dummy text ever since.</p>
</article>
<section class="cta">
  <h2>Want to Get Treated? Schedule Your Appointment Now!</h2>
  <a class="btn">Get Appointment
    <svg width="26" height="26" viewBox="0 0 26 26" aria-hidden="true" fill="none" stroke="#333" stroke-width="1.6">
      <rect x="2" y="4" width="22" height="20" rx="1"/><line x1="2" y1="9" x2="24" y2="9"/>
      <line x1="7" y1="1" x2="7" y2="6"/><line x1="19" y1="1" x2="19" y2="6"/>
      <g fill="#333" stroke="none"><rect x="6" y="12" width="3" height="2"/><rect x="11.5" y="12" width="3" height="2"/><rect x="17" y="12" width="3" height="2"/><rect x="6" y="16" width="3" height="2"/><rect x="11.5" y="16" width="3" height="2"/><rect x="17" y="16" width="3" height="2"/><rect x="6" y="20" width="3" height="2"/><rect x="11.5" y="20" width="3" height="2"/></g>
    </svg>
  </a>
</section>
<footer class="site-footer">© Copyrights 2014 All rights Reserved</footer>
</body>
</html>
```